Hartwell Estates Business Cards

I would like a business card that includes myself and my partner.
Includes: Logo, office #, email, website, our names, our numbers and possibly the address. I would also like the logo to be embossed and the card to be horizontal.
There is a photo of our yard signs to give you an idea of the colors of our business.

Target Market(s)

Everyone in real estate market.
We are in a rural area. Our clientele are from all socioeconomic backgrounds.

Industry/Entity Type

Real Estate Agent

Contact Information for Business Card

Company Name: Hartwell Estates
Our Names, Titles & Cell #'s : Dana Pembrook-Broker (555).317.6624, Marla Pembrook-Realtor (555).609.1385
Office #: (555).240.3918
Website: hartwellestates-demo.com
Joint Email: pembrook@hartwellestates-demo.com
Office Address: 418B W. Calloway Ave.
Marrow Creek, KS. 70913

Font styles to use
Serif

Requirements
Must have
• HORIZONTAL, Logo, Myself and my partners names, Our cell #'s, our office #, our website, our email address
Nice to have
• Embossed logo, office address, our titles.

```html
<!DOCTYPE html>
<html lang="en">
<head>
<meta charset="utf-8">
<title>Hartwell Estates Business Cards</title>
<link rel="stylesheet" href="https://fonts.googleapis.com/css2?family=Libre+Baskerville:wght@700&family=Open+Sans:wght@400;600&display=swap">
<style>
  :root {
    --plum: #4a2163;
    --plum-deep: #3a1650;
    --plum-light: #6a3a8a;
    --paper: #ffffff;
    --paper-shade: #eeeef1;
    --ink-grey: #555259;
    --backdrop: #e9e6e2;
  }
  * { box-sizing: border-box; margin: 0; padding: 0; }
  html, body { width: 1200px; height: 843px; overflow: hidden; }
  body {
    background: var(--backdrop);
    font-family: "Open Sans", sans-serif;
    position: relative;
  }
  .card {
    position: absolute;
    width: 560px;
    height: 320px;
    border-radius: 4px;
    overflow: hidden;
    box-shadow: 0 6px 18px rgba(0,0,0,0.18);
  }
  /* Back side */
  .card-back {
    left: 30px;
    top: 90px;
    background: linear-gradient(160deg, var(--plum-light) 0%, var(--plum) 55%, var(--plum-deep) 100%);
  }
  .card-back .wordmark {
    position: absolute;
    left: 0; right: 0;
    top: 128px;
    text-align: center;
    font-family: "Libre Baskerville", serif;
    font-weight: 700;
    font-size: 34px;
    color: var(--paper);
    letter-spacing: 1px;
  }
  .card-back .web {
    position: absolute;
    left: 0; right: 0;
    bottom: 26px;
    text-align: center;
    font-size: 13px;
    letter-spacing: 5px;
    color: var(--paper);
  }
  /* Front side */
  .card-front {
    left: 610px;
    top: 433px;
    background: linear-gradient(180deg, var(--paper) 0%, var(--paper-shade) 100%);
  }
  .people {
    position: absolute;
    left: 28px;
    top: 24px;
    color: var(--ink-grey);
  }
  .person { margin-bottom: 10px; }
  .person-name {
    font-weight: 600;
    font-size: 16px;
    color: var(--plum);
    line-height: 1.2;
  }
  .person-title, .person-phone {
    font-size: 12px;
    line-height: 1.4;
  }
  .contact-line {
    display: flex;
    align-items: center;
    gap: 7px;
    font-size: 12.5px;
    line-height: 1.6;
  }
  .contact-line svg { width: 12px; height: 12px; fill: var(--plum); flex: none; }
  .card-front .wordmark {
    position: absolute;
    right: 30px;
    top: 78px;
    font-family: "Libre Baskerville", serif;
    font-weight: 700;
    font-size: 28px;
    color: var(--plum);
  }
  .address {
    position: absolute;
    right: 30px;
    top: 196px;
    text-align: right;
    font-size: 13px;
    line-height: 1.5;
    color: var(--ink-grey);
  }
  .web-band {
    position: absolute;
    left: 0; right: 0;
    top: 246px;
    height: 30px;
    background: var(--plum);
    color: var(--paper);
    font-size: 13px;
    letter-spacing: 4px;
    line-height: 30px;
    padding-left: 36px;
  }
  .edge-strip {
    position: absolute;
    left: 0; right: 0;
    bottom: 0;
    height: 18px;
    background: var(--plum);
  }
</style>
</head>
<body>
  <section class="card card-back" aria-label="Card back">
    <div class="wordmark">Hartwell Estates</div>
    <div class="web">www.hartwellestates-demo.com</div>
  </section>

  <section class="card card-front" aria-label="Card front">
    <div class="people">
      <div class="person">
        <div class="person-name">Dana Pembrook,</div>
        <div class="person-title">Broker</div>
        <div class="person-phone">(555).317.6624</div>
      </div>
      <div class="person">
        <div class="person-name">Marla Pembrook,</div>
        <div class="person-title">Realtor</div>
        <div class="person-phone">(555).609.1385</div>
      </div>
      <div class="contact-line">
        <svg viewBox="0 0 24 24" aria-hidden="true"><path d="M6.6 10.8a15.1 15.1 0 0 0 6.6 6.6l2.2-2.2a1 1 0 0 1 1-.25 11.4 11.4 0 0 0 3.6.57 1 1 0 0 1 1 1V20a1 1 0 0 1-1 1A17 17 0 0 1 3 4a1 1 0 0 1 1-1h3.5a1 1 0 0 1 1 1c0 1.25.2 2.45.57 3.6a1 1 0 0 1-.25 1z"/></svg>
        <span>(555).240.3918</span>
      </div>
      <div class="contact-line">
        <svg viewBox="0 0 24 24" aria-hidden="true"><path d="M2 5h20v2l-10 7L2 7z"/><path d="M2 9l10 7 10-7v10H2z"/></svg>
        <span>pembrook@hartwellestates-demo.com</span>
      </div>
    </div>

    <div class="wordmark">Hartwell Estates</div>

    <div class="address">
      418B W. Calloway Ave.<br>
      Marrow Creek, KS. 70913
    </div>

    <div class="web-band">www.hartwellestates-demo.com</div>
    <div class="edge-strip"></div>
  </section>
</body>
</html>
```